Local Flower Farm Needs Business Card Design

I need business cards designed for a flower farm based in Eudora, Kansas.
Business Info:
We are a local cut flower farm located in Eudora, Kansas, founded by Corinne Haldwick. What started as a passion for agriculture and search for more joy in daily life has blossomed into a small business dedicated to providing the community with beautiful, fresh, and sustainable flowers. We specialize in local, seasonal blooms, ensuring that every petal reflects the care and dedication we pour into our craft. Our mission is to deliver the highest quality flowers directly to our customers through local farmers markets and to florists who share our commitment to sustainability. Join us in celebrating the beauty of nature, one bloom at a time!
Contact Details:
Corinne Haldwick
Owner
Phone 913-555-0147
Facebook: Rosalind Thorpe Gardens
Instagram: @RosalindThorpeGardens
Website: RosalindThorpeGardens.example
Target Market(s)
Wholesale to Florists and Direct to Consumer via Farmers Market
Industry/Entity Type
Florist, Farm
Contact Information for Business Card
Name, Contact Info, Logo
Look and feel
Each slider illustrates characteristics of the customer's brand and the style your logo design should communicate.

```html
<!DOCTYPE html>
<html lang="en">
<head>
<meta charset="utf-8">
<title>Rosalind Thorpe Gardens — Business Card</title>
<link rel="stylesheet" href="https://fonts.googleapis.com/css2?family=Libre+Baskerville&family=EB+Garamond:wght@400;500&display=swap">
<style>
  :root {
    --ink: #1b3234;
    --card: #ffffff;
    --backdrop: #2a2a2a;
    --rule: #3a4a4b;
  }
  * { box-sizing: border-box; margin: 0; padding: 0; }
  html, body {
    width: 1200px;
    height: 1200px;
    overflow: hidden;
    background: var(--backdrop);
  }
  .sheet {
    width: 1200px;
    height: 1200px;
    display: flex;
    flex-direction: column;
    align-items: center;
    justify-content: center;
    gap: 56px;
  }
  .card {
    width: 880px;
    height: 503px;
    background: var(--card);
    color: var(--ink);
    position: relative;
  }

  /* Front */
  .card--front {
    display: flex;
    flex-direction: column;
    align-items: center;
    justify-content: center;
  }
  .brand {
    display: flex;
    align-items: center;
    gap: 18px;
    margin-top: -20px;
  }
  .brand__dot {
    width: 26px;
    height: 26px;
    border: 1.5px solid var(--ink);
    border-radius: 50%;
  }
  .brand__name {
    font-family: "Libre Baskerville", serif;
    font-size: 34px;
    letter-spacing: 0.06em;
    color: var(--ink);
  }
  .front__url {
    position: absolute;
    bottom: 86px;
    left: 0;
    right: 0;
    text-align: center;
    font-family: "Libre Baskerville", serif;
    font-size: 17px;
    letter-spacing: 0.3em;
  }

  /* Back */
  .card--back {
    display: flex;
    align-items: flex-start;
    padding-left: 60px;
    padding-top: 180px;
  }
  .identity {
    flex: none;
    width: 370px;
    text-align: right;
    padding-right: 30px;
    margin-top: 6px;
  }
  .identity__name {
    font-family: "EB Garamond", serif;
    font-weight: 500;
    font-size: 26px;
    letter-spacing: 0.06em;
    text-transform: uppercase;
    white-space: nowrap;
  }
  .identity__role {
    font-family: "EB Garamond", serif;
    font-size: 21px;
    letter-spacing: 0.04em;
    margin-top: 2px;
  }
  .divider {
    flex: none;
    width: 1.5px;
    height: 150px;
    background: var(--rule);
  }
  .contacts {
    list-style: none;
    padding-left: 34px;
    margin-top: 14px;
  }
  .contacts__item {
    display: flex;
    align-items: center;
    gap: 12px;
    font-family: "EB Garamond", serif;
    font-size: 25px;
    line-height: 1.36;
    white-space: nowrap;
  }
  .contacts__icon {
    width: 22px;
    height: 22px;
    flex: none;
  }
</style>
</head>
<body>
<main class="sheet">
  <section class="card card--front" aria-label="Card front">
    <div class="brand">
      <span class="brand__dot"></span>
      <span class="brand__name">Rosalind Thorpe Gardens</span>
    </div>
    <p class="front__url">WWW.ROSALINDTHORPEGARDENS.EXAMPLE</p>
  </section>

  <section class="card card--back" aria-label="Card back">
    <div class="identity">
      <h1 class="identity__name">Corinne Haldwick</h1>
      <p class="identity__role">Owner</p>
    </div>
    <div class="divider"></div>
    <ul class="contacts">
      <li class="contacts__item">
        <svg class="contacts__icon" viewBox="0 0 22 22" aria-hidden="true">
          <circle cx="11" cy="11" r="10" fill="none" stroke="#1b3234" stroke-width="1.3"/>
          <path d="M8 6.2c.6-.4 1.2-.3 1.5.2l.8 1.5c.2.5.1 1-.3 1.2l-.6.4c.4 1.2 1.2 2.2 2.3 2.8l.5-.5c.4-.3.9-.3 1.2 0l1.3 1c.4.4.4 1 0 1.4l-.6.6c-2.7.6-6.3-3.3-6.4-6.4z" fill="#1b3234"/>
        </svg>
        913-555-0147
      </li>
      <li class="contacts__item">
        <svg class="contacts__icon" viewBox="0 0 22 22" aria-hidden="true">
          <circle cx="11" cy="11" r="10" fill="none" stroke="#1b3234" stroke-width="1.3"/>
        </svg>
        Rosalind Thorpe Gardens
      </li>
      <li class="contacts__item">
        <svg class="contacts__icon" viewBox="0 0 22 22" aria-hidden="true">
          <circle cx="11" cy="11" r="10" fill="none" stroke="#1b3234" stroke-width="1.3"/>
        </svg>
        @RosalindThorpeGardens
      </li>
      <li class="contacts__item">
        <svg class="contacts__icon" viewBox="0 0 22 22" aria-hidden="true">
          <circle cx="11" cy="11" r="10" fill="none" stroke="#1b3234" stroke-width="1.3"/>
          <circle cx="11" cy="11" r="6" fill="none" stroke="#1b3234" stroke-width="1"/>
          <ellipse cx="11" cy="11" rx="2.6" ry="6" fill="none" stroke="#1b3234" stroke-width="1"/>
          <line x1="5" y1="11" x2="17" y2="11" stroke="#1b3234" stroke-width="1"/>
        </svg>
        RosalindThorpeGardens.example
      </li>
    </ul>
  </section>
</main>
</body>
</html>
```